Home Security Company Business Card

Looking for a eye catching business card that is non traditional and stands out but yet still looks professional. It should include all the pertinent information such as name, title, address, telephone, e-mail, website address should definitely stand out and then finally the logo.

Target Market(s)

Residential and Commercial accounts mostly upscale accounts

Industry/Entity Type

Security

Contact Information for Business Card

Name
Title
Address
Office #
Cell #
E-mail
Website

Font styles to use
Serif
Sans Serif

Requirements
Must have
• Logo, two sided color configuration
Nice to have
• You decide
Should not have
• There really aren't any.

```html
<!DOCTYPE html>
<html lang="en">
<head>
<meta charset="utf-8">
<title>Ironvale Security – Business Card</title>
<link href="https://fonts.googleapis.com/css2?family=Source+Sans+3:wght@400;600&display=swap" rel="stylesheet">
<style>
  :root {
    --page-bg: #eeeae6;
    --card-white: #ffffff;
    --brand-red: #7f140a;
    --brand-red-light: #b9503a;
    --gold: #f2c23a;
    --gold-deep: #d99a1e;
    --logo-red: #8a1a0c;
    --text-light: #ffffff;
  }
  * { margin: 0; padding: 0; box-sizing: border-box; }
  html, body {
    width: 1200px; height: 900px; overflow: hidden;
    background: var(--page-bg);
    font-family: "Source Sans 3", Arial, sans-serif;
  }
  .canvas { position: relative; width: 1200px; height: 900px; }

  .card {
    position: absolute;
    overflow: hidden;
    box-shadow: 0 6px 18px rgba(0,0,0,0.18);
  }

  /* Front */
  .card-front {
    left: 238px; top: 62px; width: 555px; height: 342px;
    background: var(--card-white);
  }
  .front-curve { position: absolute; inset: 0; }
  .brand-lockup {
    position: absolute; left: 28px; top: 204px;
    display: flex; align-items: center; gap: 12px;
  }
  .brand-mark {
    width: 40px; height: 40px; border-radius: 50%;
    background: var(--logo-red);
  }
  .brand-name {
    font-family: "Source Sans 3", Arial, sans-serif;
    font-weight: 600; font-size: 21px; line-height: 1;
    color: var(--logo-red);
    white-space: nowrap;
  }

  .contact-block {
    position: absolute; right: 36px; top: 68px;
    text-align: right; color: var(--text-light);
  }
  .person-name {
    color: var(--gold); font-weight: 600; font-size: 20px;
    line-height: 24px; letter-spacing: 0.3px;
  }
  .person-title { font-size: 15px; line-height: 20px; }
  .contact-list { list-style: none; margin-top: 44px; }
  .contact-list li {
    font-size: 15px; line-height: 20px;
    display: flex; justify-content: flex-end; align-items: center; gap: 5px;
  }
  .contact-list svg { width: 10px; height: 10px; fill: var(--gold); }

  /* Back */
  .card-back {
    left: 457px; top: 518px; width: 560px; height: 343px;
    background: radial-gradient(ellipse 240px 220px at 280px 160px, var(--brand-red-light), var(--brand-red));
    color: var(--text-light); text-align: center;
  }
  .back-brand {
    position: absolute; left: 0; right: 0; top: 152px;
  }
  .back-brand .brand-name { color: var(--text-light); font-size: 28px; }
  .back-address {
    position: absolute; left: 0; right: 0; top: 282px;
    font-size: 15px;
  }
</style>
</head>
<body>
<main class="canvas">

  <section class="card card-front" aria-label="Business card front">
    <svg class="front-curve" viewBox="0 0 555 342" width="555" height="342" aria-hidden="true">
      <defs>
        <linearGradient id="goldBand" x1="0" y1="0" x2="0" y2="1">
          <stop offset="0" stop-color="#d99a1e"/>
          <stop offset="0.5" stop-color="#f2c23a"/>
          <stop offset="1" stop-color="#d99a1e"/>
        </linearGradient>
      </defs>
      <path d="M217,0 C203,150 285,290 398,342 L555,342 L555,0 Z" fill="url(#goldBand)"/>
      <path d="M232,0 C220,145 300,285 412,342 L555,342 L555,0 Z" fill="#7f140a"/>
    </svg>

    <div class="brand-lockup">
      <span class="brand-mark"></span>
      <span class="brand-name">Ironvale Security</span>
    </div>

    <div class="contact-block">
      <div class="person-name">DANIEL MARSH</div>
      <div class="person-title">Managing Director</div>
      <ul class="contact-list">
        <li>055-987 321 654
          <svg viewBox="0 0 10 10"><path d="M1 4 Q5 0 9 4 L8 5 L6.5 4 L6.5 3 Q5 2.5 3.5 3 L3.5 4 L2 5 Z M2 6 H8 V9 H2 Z"/></svg></li>
        <li>055-987 321 655
          <svg viewBox="0 0 10 10"><path d="M3 0.5 H7 V9.5 H3 Z M3.8 1.5 V7.5 H6.2 V1.5 Z"/></svg></li>
        <li>hello@ironvale.example
          <svg viewBox="0 0 10 10"><path d="M0.5 2 H9.5 V8 H0.5 Z M1.2 2.6 L5 5.4 L8.8 2.6 Z"/></svg></li>
        <li>www.ironvale.example
          <svg viewBox="0 0 10 10"><path d="M2 8 L1 7 L4 4 L5 5 L4.3 5.7 L4 5.4 L2 7.4 L2.6 8 L4.6 6 L5.3 6.7 Z M8 2 L9 3 L6 6 L5 5 L5.7 4.3 L6 4.6 L8 2.6 L7.4 2 L5.4 4 L4.7 3.3 Z"/></svg></li>
      </ul>
    </div>
  </section>

  <section class="card card-back" aria-label="Business card back">
    <div class="back-brand">
      <span class="brand-name">Ironvale Security</span>
    </div>
    <p class="back-address">48 Harbor Lane, Westbrook, Northland, 204817.</p>
  </section>

</main>
</body>
</html>
```